We are a recruitment company based in Norwich/Cambridge England.
I have included our company logo which we want to remain the same.

What we are looking for is a new creative Business card which will really stand out!!

Contact Information for Business Card

Harriet Dunmore
email: Harriet@plavex.co.uk
Address: Brackwell House
Fenmoor Enterprise Park
Partridge Way
Norwich
QB9 3KX
Tel:01632 960418

```html
<!DOCTYPE html>
<html lang="en">
<head>
<meta charset="utf-8">
<title>Plavex Business Card</title>
<link rel="stylesheet" href="https://fonts.googleapis.com/css2?family=Lato:wght@400;700&display=swap">
<style>
  :root {
    --green: #7dc242;
    --grey: #8f8e93;
    --ink: #4a4a4d;
    --card: #ffffff;
    --backdrop: #e9e7e3;
  }
  * { margin: 0; padding: 0; box-sizing: border-box; }
  html, body {
    width: 1200px; height: 886px; overflow: hidden;
    background: var(--backdrop);
    font-family: "Lato", sans-serif;
  }
  .stage {
    position: relative; width: 1200px; height: 886px;
    display: flex; justify-content: center; align-items: center; gap: 120px;
  }
  .card {
    position: relative; width: 320px; height: 560px;
    background: var(--card); border-radius: 18px; overflow: hidden;
    box-shadow: 0 8px 24px rgba(0,0,0,0.12);
  }
  .card-front .details {
    position: absolute; top: 70px; left: 0; right: 0;
    text-align: center; padding: 0 20px;
  }
  .name {
    color: var(--green); font-size: 28px; font-weight: 400;
    text-transform: uppercase; letter-spacing: 0.5px; line-height: 1.1;
  }
  .role {
    color: var(--grey); font-size: 17px; text-transform: uppercase;
    letter-spacing: 0.5px; margin-top: 2px;
  }
  .rule {
    width: 38px; height: 2px; background: var(--green);
    margin: 14px auto 18px;
  }
  .contact {
    color: var(--ink); font-size: 13px; line-height: 1.6;
    font-style: normal;
  }
  .decor {
    position: absolute; left: 0; bottom: 0; width: 320px; height: 300px;
  }
  .card-back {
    display: flex; flex-direction: column; justify-content: center; align-items: center;
  }
  .brand {
    display: flex; align-items: center; gap: 12px;
  }
  .brand-dot {
    width: 34px; height: 34px; border-radius: 50%; background: var(--grey);
  }
  .brand-name {
    color: var(--green); font-size: 52px; font-weight: 700; line-height: 1;
  }
  .tagline {
    color: var(--grey); font-size: 10px; letter-spacing: 3px;
    margin-top: 10px; padding-left: 46px;
  }
</style>
</head>
<body>
<main class="stage">
  <section class="card card-front">
    <div class="details">
      <h1 class="name">Harriet Dunmore</h1>
      <p class="role">CEO/Founder</p>
      <div class="rule"></div>
      <address class="contact">
        Brackwell House, Fenmoor Enterprise Park<br>
        Partridge Way, Norwich QB9 3KX<br>
        01632 960418 &nbsp;|&nbsp; Harriet@plavex.co.uk<br>
        www.plavex.co.uk
      </address>
    </div>
    <svg class="decor" viewBox="0 0 320 300" aria-hidden="true">
      <circle cx="90" cy="300" r="190" fill="var(--green)"/>
    </svg>
  </section>
  <section class="card card-back">
    <div class="brand">
      <span class="brand-dot"></span>
      <span class="brand-name">Plavex</span>
    </div>
    <p class="tagline">Technology Recruitment</p>
  </section>
</main>
</body>
</html>
```